Letterhead, stationery and email signature for construction business

I need the letterhead, stationery and email signature designs for a construction business. I want them to have a corporate feel to them.

I've attached the logo for reference.

```html
<!DOCTYPE html>
<html lang="en">
<head>
<meta charset="utf-8">
<title>Norvale Projects – Stationery Set</title>
<link href="https://fonts.googleapis.com/css2?family=Open+Sans:wght@400;600&family=Roboto:wght@400;500;700&display=swap" rel="stylesheet">
<style>
  :root {
    --bg: #e8e8e8;
    --paper: #f1f1f1;
    --brand-blue: #3b5ea8;
    --folder-blue: #2f5fa9;
    --folder-deep: #264c94;
    --ink: #555a60;
    --ink-soft: #6a6e73;
    --white: #ffffff;
  }
  * { margin: 0; padding: 0; box-sizing: border-box; }
  html, body { width: 1200px; height: 795px; overflow: hidden; background: var(--bg); }
  .canvas { position: relative; width: 1200px; height: 795px; background: var(--bg); font-family: "Open Sans", Arial, sans-serif; }

  .sheet { position: absolute; background: var(--paper); overflow: hidden; }

  /* wordmark */
  .wordmark { display: flex; align-items: center; gap: 4px; font-family: "Roboto", Arial, sans-serif; font-weight: 700; color: var(--brand-blue); white-space: nowrap; letter-spacing: 0.02em; }
  .wordmark .mark-square { display: block; background: currentColor; flex: none; }
  .wordmark--light { color: var(--white); }

  /* letterhead */
  .letterhead { left: 292px; top: 99px; width: 293px; height: 415px; }
  .letterhead .wordmark { position: absolute; left: 0; right: 0; top: 25px; justify-content: center; font-size: 13px; }
  .letterhead .mark-square { width: 12px; height: 12px; }
  .letter-body { position: absolute; left: 29px; width: 236px; top: 100px; font-size: 5.3px; line-height: 7.85px; color: var(--ink); }
  .letter-body p { text-align: justify; margin-bottom: 7.8px; }
  .letter-body .salutation { margin-bottom: 8px; }
  .letter-footer { position: absolute; left: 0; right: 0; top: 374px; text-align: center; font-family: "Roboto", Arial, sans-serif; font-size: 6.2px; line-height: 7.9px; color: var(--ink); }
  .letter-footer .company { color: var(--brand-blue); }
  .letter-footer .contact { display: inline-flex; align-items: center; gap: 2px; margin: 0 1.5px; }
  .letter-footer svg { width: 5.5px; height: 5.5px; fill: var(--brand-blue); }

  /* folder */
  .folder { left: 637px; top: 80px; width: 346px; height: 437px; background: linear-gradient(160deg, #2d5aa4 0%, var(--folder-blue) 45%, #3a6db3 65%, var(--folder-deep) 100%); }
  .folder .wordmark { position: absolute; left: 82px; top: 131px; font-size: 22px; }
  .folder .mark-square { width: 22px; height: 22px; }

  /* business cards */
  .card-back { left: 187px; top: 551px; width: 132px; height: 75px; background: var(--brand-blue); }
  .card-front { left: 187px; top: 646px; width: 132px; height: 75px; }
  .card-front .wordmark { position: absolute; right: 10px; top: 12px; font-size: 8px; }
  .card-front .mark-square { width: 8px; height: 8px; }
  .card-front .accent { position: absolute; left: 0; top: 30px; width: 3px; height: 7px; background: var(--brand-blue); }
  .card-person { position: absolute; left: 10px; top: 29px; font-family: "Roboto", Arial, sans-serif; }
  .card-person .name { font-size: 5.4px; font-weight: 700; color: var(--brand-blue); line-height: 6px; }
  .card-person .role { font-size: 3.4px; font-weight: 500; color: var(--brand-blue); line-height: 4px; }
  .card-person .address { margin-top: 4px; font-size: 3.1px; line-height: 4px; color: var(--ink); }
  .card-contacts { position: absolute; left: 10px; top: 56px; display: flex; gap: 4px; font-family: "Roboto", Arial, sans-serif; font-size: 3.1px; line-height: 4.4px; color: var(--ink); white-space: nowrap; }
  .card-contacts .col + .col { border-left: 0.5px solid var(--ink-soft); padding-left: 3px; }

  /* envelopes */
  .envelope-dl { left: 353px; top: 562px; width: 329px; height: 156px; }
  .envelope-dl .wordmark { position: absolute; left: 19px; top: 19px; font-size: 12.5px; }
  .envelope-dl .mark-square { width: 11px; height: 11px; }
  .envelope-dl .return-address { position: absolute; left: 18px; top: 44px; width: 88px; text-align: center; font-family: "Roboto", Arial, sans-serif; font-size: 6.1px; line-height: 7.4px; color: var(--ink); }

  .envelope-flap { left: 713px; top: 562px; width: 329px; height: 156px; }
  .envelope-flap .flap { position: absolute; left: 0; top: 0; width: 329px; height: 56px; }
  .envelope-flap .wordmark { position: absolute; left: 0; right: 0; top: 18px; justify-content: center; font-size: 14px; }
  .envelope-flap .mark-square { width: 13px; height: 13px; }
</style>
</head>
<body>
<main class="canvas">

  <section class="sheet letterhead" aria-label="Letterhead">
    <div class="wordmark"><span class="mark-square"></span>NORVALE PROJECTS</div>
    <div class="letter-body">
      <p class="salutation">Dear customer,</p>
      <p>Lorem ipsum dolor sit amet, consectetur adipisicing elit, sed do eiusmod tempor incididunt ut labore et dolore magna aliqua. Ut enim ad minim veniam, quis nostrud exercitation ullamco laboris nisi ut aliquip ex ea commodo consequat. Duis aute irure dolor in reprehenderit in voluptate velit esse cillum dolore eu fugiat nulla pariatur. Excepteur sint occaecat cupidatat non proident, sunt in culpa qui officia deserunt mollit anim id est laborum.</p>
      <p>Lorem ipsum dolor sit amet, consectetur adipisicing elit, sed do eiusmod tempor incididunt ut labore et dolore magna aliqua. Ut enim ad minim veniam, quis nostrud exercitation ullamco laboris nisi ut aliquip ex ea commodo consequat. Duis aute irure dolor in reprehenderit in voluptate velit esse cillum dolore eu fugiat nulla pariatur. Excepteur sint occaecat cupidatat non proident, sunt in culpa qui officia deserunt mollit anim id est laborum.</p>
      <p>Lorem ipsum dolor sit amet, consectetur adipisicing elit, sed do eiusmod tempor incididunt ut labore et dolore magna aliqua. Ut enim ad minim veniam, quis nostrud exercitation ullamco laboris nisi ut aliquip ex ea commodo consequat. Duis aute irure dolor in reprehenderit in voluptate velit esse cillum dolore eu fugiat nulla pariatur. Excepteur sint occaecat cupidatat non proident, sunt in culpa qui officia deserunt mollit anim id est laborum.</p>
      <p>Lorem ipsum dolor sit amet, consectetur adipisicing elit, sed do eiusmod tempor incididunt ut labore et dolore magna aliqua. Ut enim ad minim veniam, quis nostrud exercitation ullamco laboris nisi ut aliquip ex ea commodo consequat. Duis aute irure dolor in reprehenderit.</p>
      <p>Yours Sincerely,</p>
    </div>
    <div class="letter-footer">
      <div class="company">Norvale Projects, Ltd.</div>
      <div>4120 Harbor Ridge Road, Marlow, CA 90412</div>
      <div>
        <span class="contact"><svg viewBox="0 0 24 24" aria-hidden="true"><path d="M6.6 10.8a15.1 15.1 0 0 0 6.6 6.6l2.2-2.2a1 1 0 0 1 1-.25 11.4 11.4 0 0 0 3.6.57 1 1 0 0 1 1 1V20a1 1 0 0 1-1 1A17 17 0 0 1 3 4a1 1 0 0 1 1-1h3.5a1 1 0 0 1 1 1c0 1.250.2 2.450.57 3.57a1 1 0 0 1-.25 1z"/></svg>(555) 310-0142</span>
        <span class="contact"><svg viewBox="0 0 24 24" aria-hidden="true"><path d="M2 5h20v14H2zm2 2v.5l8 5 8-5V7zm0 2.8V17h16V9.8l-8 5z"/></svg>info@norvaleprojects.com</span>
        <span class="contact"><svg viewBox="0 0 24 24" aria-hidden="true"><path d="M12 2a10 10 0 1 0 0 20 10 10 0 0 0 0-20zm0 2a8 8 0 0 1 0 16 8 8 0 0 1 0-16zM4 11h16v2H4zm7-7h2v16h-2z"/></svg>www.norvaleprojects.com</span>
      </div>
    </div>
  </section>

  <section class="sheet folder" role="img" aria-label="Folder cover: blue-toned upward view of office towers and a construction crane">
    <div class="wordmark wordmark--light"><span class="mark-square"></span>NORVALE PROJECTS</div>
  </section>

  <section class="sheet card-back" role="img" aria-label="Business card back: brand-blue field with repeating brand pattern"></section>

  <section class="sheet card-front" aria-label="Business card front">
    <div class="wordmark"><span class="mark-square"></span>NORVALE PROJECTS</div>
    <span class="accent"></span>
    <div class="card-person">
      <div class="name">Daniel Hart</div>
      <div class="role">President</div>
      <div class="address">Kestrel House, 14 Elm Row<br>London SE4 7QT</div>
    </div>
    <div class="card-contacts">
      <div class="col">☏ (555) 418-9031<br>⎙ (555) 418-9056</div>
      <div class="col">✉ info@norvaleprojects.com<br>◍ www.norvaleprojects.com</div>
    </div>
  </section>

  <section class="sheet envelope-dl" aria-label="Envelope front">
    <div class="wordmark"><span class="mark-square"></span>NORVALE PROJECTS</div>
    <div class="return-address">Norvale Projects, Ltd.<br>4120 Harbor Ridge Road<br>Marlow, CA 90412</div>
  </section>

  <section class="sheet envelope-flap" aria-label="Envelope back">
    <svg class="flap" viewBox="0 0 329 56" aria-hidden="true"><path d="M0 0H329L323 48Q322 55 314 55H15Q8 55 7 48Z" fill="var(--brand-blue)"/></svg>
    <div class="wordmark wordmark--light"><span class="mark-square"></span>NORVALE PROJECTS</div>
  </section>

</main>
</body>
</html>
```